Brightfen Business Card Redesign & Logo Update

We need to update our business cards to something more modern and fresh. Brightfen can provide the current color schemes and old design examples, but welcome creativity in helping us with this redesign. PLEASE NOTE that we no longer utilize the "tree" and/or "leaf" imagery in our branding. If able would apprecaite an update on the quality of our "words only" logo in Ai. / PNG formats too.

Target Market(s)

Investors, landowners, corporate partners, contractors

Industry/Entity Type

Environmental Restoration & Conservation

Contact Information for Business Card

Logo, persons name, title, mailing address, phone and email, website url

Font styles to use
Other font styles liked:
• Merriweather

Requirements
Nice to have
• Logo, persons name, title, mailing address, phone and email, website url, but open to ideams
Should not have
• No all back backgrounds

```html
<!DOCTYPE html>
<html lang="en">
<head>
<meta charset="utf-8">
<title>Brightfen Business Card</title>
<link href="https://fonts.googleapis.com/css2?family=Montserrat:wght@400;500;700&family=Oswald:wght@500;700&display=swap" rel="stylesheet">
<style>
  :root {
    --orange: #eb7e24;
    --green: #157f3c;
    --ink: #1f1f1f;
    --paper: #ffffff;
    --backdrop: #e6e6e6;
  }
  * { margin: 0; padding: 0; box-sizing: border-box; }
  html, body { width: 1200px; height: 960px; overflow: hidden; }
  body {
    background: var(--backdrop);
    font-family: "Montserrat", Arial, sans-serif;
    position: relative;
  }
  .card {
    position: absolute;
    left: 240px;
    width: 720px;
    height: 412px;
    border-radius: 24px;
    overflow: hidden;
    box-shadow: 0 10px 26px rgba(0,0,0,0.18);
  }
  .card-front { top: 36px; background: var(--orange); }
  .card-back { top: 512px; background: var(--paper); }

  .brand-name {
    font-family: "Oswald", "Arial Narrow", sans-serif;
    font-weight: 700;
    letter-spacing: 2px;
    line-height: 1;
    text-transform: uppercase;
  }
  .brand-tagline {
    font-family: "Oswald", "Arial Narrow", sans-serif;
    font-weight: 500;
    text-transform: uppercase;
    letter-spacing: 1px;
  }

  .front-logo {
    position: absolute;
    left: 0; right: 0; top: 118px;
    text-align: center;
    color: var(--paper);
  }
  .front-logo .brand-name { font-size: 118px; }
  .front-logo .brand-tagline { font-size: 27px; margin-top: 8px; }

  .back-wave { position: absolute; inset: 0; }

  .back-logo {
    position: absolute;
    right: 40px; top: 40px;
    text-align: right;
  }
  .back-logo .brand-name { font-size: 64px; color: var(--green); }
  .back-logo .brand-tagline { font-size: 15px; color: var(--ink); margin-top: 4px; }

  .contact { position: absolute; left: 50px; top: 112px; color: var(--ink); }
  .person-name { font-size: 24px; font-weight: 700; text-transform: uppercase; letter-spacing: 0.5px; line-height: 30px; }
  .person-name .first { color: var(--green); }
  .person-name .last { color: var(--orange); }
  .person-title { font-size: 15px; line-height: 20px; margin-top: 2px; }
  .address { font-size: 15px; line-height: 20px; margin-top: 14px; }
  .channels { list-style: none; margin-top: 12px; }
  .channels li { display: flex; align-items: center; gap: 12px; font-size: 17px; font-weight: 500; height: 30px; }
  .channel-icon { width: 24px; height: 24px; flex: none; }
</style>
</head>
<body>

<section class="card card-front" aria-label="Card front">
  <div class="front-logo">
    <div class="brand-name">Brightfen</div>
    <div class="brand-tagline">Environmental Credit Company</div>
  </div>
</section>

<section class="card card-back" aria-label="Card back">
  <svg class="back-wave" viewBox="0 0 720 412" aria-hidden="true">
    <path d="M720,150 C610,160 545,210 495,275 C430,350 250,384 0,394 L0,412 L720,412 Z" fill="var(--orange)"/>
    <path d="M0,356 C190,354 380,330 482,276 C405,336 225,370 0,382 Z" fill="var(--green)"/>
  </svg>

  <div class="back-logo">
    <div class="brand-name">Brightfen</div>
    <div class="brand-tagline">Environmental Credit Company</div>
  </div>

  <div class="contact">
    <div class="person-name"><span class="first">Dana</span> <span class="last">Holloway</span></div>
    <div class="person-title">Managing Director</div>
    <div class="address">42 Fernhill Road 8<br>Ashford, VT 05601</div>
    <ul class="channels">
      <li>
        <svg class="channel-icon" viewBox="0 0 24 24" aria-hidden="true">
          <circle cx="12" cy="12" r="12" fill="var(--orange)"/>
          <path d="M8.5 6.5l2 2-1.2 1.6c.8 1.6 2 2.8 3.6 3.6l1.6-1.2 2 2-1.4 1.8c-3.8-.4-7.4-4-7.8-7.8z" fill="#fff"/>
        </svg>
        555-014-2286
      </li>
      <li>
        <svg class="channel-icon" viewBox="0 0 24 24" aria-hidden="true">
          <circle cx="12" cy="12" r="12" fill="var(--orange)"/>
          <rect x="6" y="8" width="12" height="8.5" rx="1" fill="#fff"/>
          <path d="M6.3 8.4L12 13l5.7-4.6" fill="none" stroke="var(--orange)" stroke-width="1.2"/>
        </svg>
        info@brightfen.com
      </li>
      <li>
        <svg class="channel-icon" viewBox="0 0 24 24" aria-hidden="true">
          <circle cx="12" cy="12" r="12" fill="var(--orange)"/>
          <circle cx="12" cy="12" r="6" fill="none" stroke="#fff" stroke-width="1.4"/>
          <ellipse cx="12" cy="12" rx="2.6" ry="6" fill="none" stroke="#fff" stroke-width="1.2"/>
          <path d="M6 12h12" stroke="#fff" stroke-width="1.2"/>
        </svg>
        www.brightfen.com
      </li>
    </ul>
  </div>
</section>

</body>
</html>
```